Pet sitting Business needs a website

We need a website that shows our services and prices. Shows our love of animals but also our professionalism. want a gallery, about, blog, services, links to fb and instagram accounts, newsletter archive. want it to be easy to access and wonderful to navigate. want the domain to be Birchfordpawhaven.com
take any info from FB site www.facebook.com/birchfordpawhaven
I would like it to fit square space platform

Target Market(s)

upscale area, responsible pet owners,

Industry/Entity Type

Pet Care

Coding

Coded - Design and coding required

Number of Pages Required

5+ page

Font styles to use
Sans Serif

Requirements
Must have
• (square space platform)
• Menu
• photo gallery
• about us
• services
• policies
• monthly newsletter
• unavailable dates
• Introduction (welcome)
• payment methods
• Daily updates
• testimonials (use from fb site)
Should not have
• stock photos

```html
<!DOCTYPE html>
<html lang="en">
<head>
<meta charset="utf-8">
<title>Birchford Paw Haven – Pet Sitting</title>
<link rel="stylesheet" href="https://fonts.googleapis.com/css2?family=Montserrat:wght@400;500;600&family=Open+Sans:ital,wght@0,400;0,600;1,400&display=swap">
<style>
:root{
  --blue:#0a80b2;
  --blue-deep:#066a98;
  --blue-heading:#1b86b6;
  --footer:#0b5a80;
  --footer-bottom:#08476a;
  --orange:#e3a113;
  --orange-text:#d8991a;
  --ink:#444;
  --muted:#666;
  --white:#fff;
}
*{margin:0;padding:0;box-sizing:border-box}
html,body{width:1200px;height:2403px;overflow:hidden;background:var(--white)}
body{position:relative;font-family:"Open Sans",Arial,sans-serif;color:var(--ink)}
.abs{position:absolute}
a{color:inherit;text-decoration:none}

/* header */
.topbar{left:0;top:0;width:1200px;height:87px}
.toplinks{right:138px;top:10px;font-family:"Montserrat",sans-serif;font-size:13px;color:#555}
.toplinks span{margin:0 6px}
.phone{right:135px;top:46px;font-family:"Montserrat",sans-serif;font-size:21px;color:#555;display:flex;align-items:center;gap:6px}
.navbar{left:0;top:87px;width:1200px;height:44px;background:linear-gradient(#1592c4,var(--blue-deep))}
.nav{left:388px;top:87px;height:44px;display:flex;align-items:center;gap:20px;font-family:"Montserrat",sans-serif;font-weight:500;font-size:14.5px;color:var(--white)}
.brand-tab{left:135px;top:0;width:217px;height:160px;background:var(--white);border-radius:0 0 110px 110px/0 0 30px 30px;box-shadow:0 2px 4px rgba(0,0,0,.15);display:flex;flex-direction:column;align-items:center;justify-content:center;gap:8px}
.brand-mark{width:38px;height:38px;border-radius:50%;background:var(--orange)}
.brand-name{font-family:"Montserrat",sans-serif;font-weight:500;font-size:19px;color:var(--orange-text);text-align:center;line-height:1.15}

/* hero */
.hero{left:0;top:131px;width:1200px;height:457px;background:linear-gradient(180deg,#8c8a82 0%,#6b5b4a 45%,#4a3b2e 100%)}
.hero-callout{left:117px;top:293px;width:440px;height:124px;background:rgba(227,161,19,.92);border-radius:14px 60px 60px 14px;display:flex;align-items:center;gap:20px;padding-left:40px;color:var(--white);font-family:"Montserrat",sans-serif}
.hero-callout .dot{width:56px;height:56px;border-radius:50%;border:3px solid var(--white);flex:none}
.hero-callout p{font-size:23px;line-height:1.25}
.hero-callout p b{font-weight:400;font-size:32px;display:block}
.dots{left:558px;top:553px;display:flex;gap:5px}
.dots i{width:18px;height:18px;border-radius:50%;border:2px solid var(--white);background:rgba(255,255,255,.9)}
.dots i:first-child{background:transparent}

/* about */
.about-ring{left:125px;top:628px;width:284px;height:284px;border-radius:50%;border:2px solid var(--blue);padding:8px}
.about-photo{width:100%;height:100%;border-radius:50%;background:radial-gradient(circle at 40% 45%,#f2eeea 0%,#d9d2ca 45%,#6b5242 80%,#3a2a20 100%)}
.about-title{left:429px;top:648px;font-family:"Montserrat",sans-serif;font-size:33px;color:var(--blue-heading)}
.about-text{left:429px;top:710px;width:640px;font-size:13px;line-height:27px;color:var(--muted)}
.about-text p+p{margin-top:12px}

/* badges */
.badge{width:84px;height:48px;background:var(--white);border-radius:0 0 42px 42px;display:flex;justify-content:center;align-items:flex-start;padding-top:6px}
.badge i{width:34px;height:34px;border-radius:50%;background:var(--orange)}

/* services */
.services{left:0;top:961px;width:1200px;height:365px;background:linear-gradient(180deg,rgba(227,161,19,.93),rgba(221,156,12,.95)),linear-gradient(#8a7a3a,#6e5c20)}
.section-title{width:1200px;text-align:center;font-family:"Montserrat",sans-serif;font-size:25px}
.service{width:240px;text-align:center;color:var(--white)}
.service .icon{width:102px;height:102px;border-radius:50%;border:2px solid var(--white);margin:0 auto;display:flex;align-items:center;justify-content:center}
.service h3{font-family:"Montserrat",sans-serif;font-weight:500;font-size:16px;margin-top:20px}
.service p{font-size:11px;line-height:19px;margin-top:6px;height:38px}
.service .more{display:inline-block;margin-top:12px;width:110px;height:34px;line-height:30px;border:2px solid var(--white);font-family:"Montserrat",sans-serif;font-size:12.5px}

/* news */
.news{width:282px}
.news .thumb{width:282px;height:152px}
.news h3{font-family:"Montserrat",sans-serif;font-weight:400;font-size:16.5px;color:var(--blue-heading);margin-top:14px;line-height:23px}
.news p{font-size:11.5px;line-height:21px;color:var(--muted);margin-top:6px}
.news .more{font-size:12.5px;color:#333;display:block;margin-top:4px}

/* testimonials */
.testimonials{left:0;top:1767px;width:1200px;height:328px;background:var(--blue)}
.quote{left:230px;top:1880px;width:740px;text-align:center;font-style:italic;font-size:19px;line-height:32px;color:var(--white)}
.qmark{font-family:Georgia,serif;font-size:56px;color:#cfe6f1;line-height:1}
.author{left:506px;top:1997px;display:flex;align-items:center;gap:10px;color:var(--white)}
.author .avatar{width:54px;height:54px;border-radius:50%;border:3px solid #e6f2f8;background:linear-gradient(#f0d5b8,#c9a07a)}
.author b{font-family:"Montserrat",sans-serif;font-weight:500;font-size:16px;display:block}
.author span{font-size:13px}

/* footer */
.footer{left:0;top:2095px;width:1200px;height:247px;background:var(--footer)}
.footer-brand{left:136px;top:2160px;width:200px;display:flex;flex-direction:column;align-items:center;gap:10px;opacity:.55}
.footer-brand i{width:44px;height:44px;border-radius:50%;background:#9fc6d8}
.footer-brand span{font-family:"Montserrat",sans-serif;font-size:21px;color:#cfe3ec;text-align:center;line-height:1.15}
.fcol{color:var(--white)}
.fcol h4{font-family:"Montserrat",sans-serif;font-weight:500;font-size:16px;margin-bottom:10px}
.fcol li{list-style:none;font-size:13px;line-height:26px;padding-left:4px}
.fcol p{font-size:13px;margin-bottom:10px}
.social{display:flex;gap:10px}
.social i{width:36px;height:36px;border-radius:50%;background:var(--white)}
.bottombar{left:0;top:2342px;width:1200px;height:61px;background:var(--footer-bottom);text-align:center;line-height:61px;font-size:11.5px;color:#b6d0dd}
</style>
</head>
<body>

<header>
  <div class="abs topbar"></div>
  <div class="abs toplinks"><a href="#">Policies</a><span>|</span><a href="#">Unavailable Dates</a></div>
  <div class="abs phone">
    <svg width="18" height="18" viewBox="0 0 24 24"><path fill="#e3a113" d="M6.6 10.8a15.2 15.2 0 0 0 6.6 6.6l2.2-2.2a1 1 0 0 1 1-.25 11.4 11.4 0 0 0 3.6.57 1 1 0 0 1 1 1V20a1 1 0 0 1-1 1A17 17 0 0 1 3 4a1 1 0 0 1 1-1h3.5a1 1 0 0 1 1 1c0 1.25.2 2.45.57 3.57a1 1 0 0 1-.25 1z"/></svg>
    555.204.7716
  </div>
  <div class="abs navbar"></div>
  <nav class="abs nav">
    <a href="#">Photo gallery</a><a href="#">About us</a><a href="#">Services</a><a href="#">Monthly newsletter</a><a href="#">Introduction</a><a href="#">Payment methods</a>
  </nav>
  <div class="abs brand-tab">
    <i class="brand-mark"></i>
    <div class="brand-name">Birchford<br>Paw Haven</div>
  </div>
</header>

<section>
  <div class="abs hero" role="img" aria-label="Photo of a pet sitter walking a group of leashed dachshunds and beagles on a city sidewalk"></div>
  <div class="abs hero-callout"><i class="dot"></i><p>We provide Professional<b>Pet sitting Services</b></p></div>
  <div class="abs dots"><i></i><i></i><i></i><i></i></div>
</section>

<section>
  <div class="abs about-ring"><div class="about-photo" role="img" aria-label="Photo of a veterinary technician examining a small dog with a stethoscope"></div></div>
  <h2 class="abs about-title" style="font-weight:400">About Birchford Paw Haven</h2>
  <div class="abs about-text">
    <p>Hi my name is Dana Whitcomb and I would love to introduce myself. I am a Licensed Veterinarian Technician from Nashville, Tennessee. My family and I moved to San Antonio in 2008.</p>
    <p>I have dedicated the last 13 years to raising my 2 beautiful children and 5 of my furry babies. I have the knowledge and the training to give the special care your pet will need. I was a Licensed Veterinarian Technician Supervisor of a major animal hospital in Nashville. I have spent 20 years of my life taking care of our friends and would to</p>
  </div>
</section>

<div class="abs badge" style="left:558px;top:913px;border-radius:42px 42px 0 0;padding-top:8px;height:48px"><i></i></div>

<section>
  <div class="abs services" role="img" aria-label="Background photo of a person walking a dog across a grassy field, tinted golden"></div>
  <h2 class="abs section-title" style="left:0;top:990px;font-weight:400;color:var(--white)">Our Services</h2>

  <div class="abs service" style="left:131px;top:1043px">
    <div class="icon"><svg width="48" height="48" viewBox="0 0 48 48" fill="#fff"><ellipse cx="24" cy="32" rx="11" ry="9"/><ellipse cx="11" cy="20" rx="4.5" ry="6"/><ellipse cx="19" cy="12" rx="4.5" ry="6"/><ellipse cx="29" cy="12" rx="4.5" ry="6"/><ellipse cx="37" cy="20" rx="4.5" ry="6"/></svg></div>
    <h3>Daily Visit</h3>
    <p>No additional charge for each pet<br>Dog walks or play time for your pet</p>
    <a class="more" href="#">Read More</a>
  </div>

  <div class="abs service" style="left:370px;top:1043px">
    <div class="icon"><svg width="52" height="52" viewBox="0 0 52 52" fill="#fff"><rect x="12" y="22" width="24" height="11" rx="5"/><rect x="13" y="31" width="4" height="12"/><rect x="30" y="31" width="4" height="12"/><circle cx="38" cy="18" r="6"/><rect x="7" y="20" width="7" height="3" rx="1.5"/><path d="M42 8 L30 22" stroke="#fff" stroke-width="2" fill="none"/></svg></div>
    <h3>Potty Visits</h3>
    <p>Usually done at noon and bedtime<br>letting them out to potty</p>
    <a class="more" href="#">Read More</a>
  </div>

  <div class="abs service" style="left:612px;top:1043px">
    <div class="icon"><svg width="52" height="52" viewBox="0 0 52 52" fill="none" stroke="#fff" stroke-width="3" stroke-linecap="round"><path d="M14 38 L34 18"/><rect x="18" y="16" width="22" height="9" rx="2" transform="rotate(-45 29 20)"/><path d="M36 10 L42 16 M39 13 L44 8"/><path d="M14 38 L8 44"/></svg></div>
    <h3>Medication</h3>
    <p>Injections or subcutaneous fluids $5<br>per administration</p>
    <a class="more" href="#">Read More</a>
  </div>

  <div class="abs service" style="left:849px;top:1043px">
    <div class="icon"><svg width="52" height="52" viewBox="0 0 52 52" fill="#fff"><rect x="20" y="10" width="12" height="6" rx="1"/><path d="M14 18 h24 l4 10 v12 h-32 v-12z"/><rect x="12" y="38" width="6" height="6" rx="1"/><rect x="34" y="38" width="6" height="6" rx="1"/><circle cx="18" cy="32" r="2.5" fill="#e3a113"/><circle cx="34" cy="32" r="2.5" fill="#e3a113"/><rect x="17" y="21" width="18" height="6" fill="#e3a113"/></svg></div>
    <h3>Pet Taxi</h3>
    <p>Grooming, vet drop off/pic up<br>$10.00 each trip</p>
    <a class="more" href="#">Read More</a>
  </div>
</section>

<section>
  <h2 class="abs section-title" style="left:0;top:1364px;font-weight:400;font-size:27px;color:var(--orange-text)">Club News</h2>

  <article class="abs news" style="left:144px;top:1418px">
    <div class="thumb" role="img" aria-label="Photo of a tabby kitten lying on its back" style="background:linear-gradient(135deg,#d8cdbf,#9c8a78 60%,#6e5f52)"></div>
    <h3>Summer is almost over</h3>
    <p>Wow! Can you believe it? Summer is almost over and School starts this month on August 22nd! My kids are ready and I know I am.</p>
    <a class="more" href="#">Read More</a>
  </article>

  <article class="abs news" style="left:461px;top:1418px">
    <div class="thumb" role="img" aria-label="Photo of a German shepherd in a harness standing on grass" style="background:linear-gradient(180deg,#7fa04a,#5d8a30 60%,#3f6a22)"></div>
    <h3>Now There's A Company That Will Make Sure Your Pet Is Cared</h3>
    <p>It's the last thing we want to think about: what will happen to our dogs if we die before they do</p>
    <a class="more" href="#">Read More</a>
  </article>

  <article class="abs news" style="left:779px;top:1418px">
    <div class="thumb" role="img" aria-label="Photo of a spaniel puppy looking at the camera" style="background:linear-gradient(135deg,#4a5a3c,#a77a55 55%,#efe8e0)"></div>
    <h3>PawLink  which only works with cats</h3>
    <p>which only works with cats and dogs now — has two different service plans, depending on your age and needs</p>
    <a class="more" href="#">Read More</a>
  </article>
</section>

<div class="abs badge" style="left:558px;top:1719px;border-radius:42px 42px 0 0;padding-top:8px;height:48px"><i></i></div>

<section>
  <div class="abs testimonials"></div>
  <h2 class="abs section-title" style="left:0;top:1834px;font-weight:400;font-size:28px;color:var(--white)">Testimonials</h2>
  <span class="abs qmark" style="left:218px;top:1858px">&ldquo;</span>
  <span class="abs qmark" style="left:948px;top:1858px">&rdquo;</span>
  <p class="abs quote">Fusce ultricies orci ac feugiat suscipit leo massa sodales velit et scelerisque mi tortor at ipsum cligula augue bibendum accumsan vestibulum ut commodo a mi Morbi ornare gravida elit Integer congue augue et malesuada</p>
  <div class="abs author">
    <div class="avatar" role="img" aria-label="Portrait photo of the reviewer"></div>
    <div><b>By Author Name</b><span>City Name</span></div>
  </div>
</section>

<footer>
  <div class="abs footer"></div>
  <div class="abs footer-brand"><i></i><span>Birchford<br>Paw Haven</span></div>

  <div class="abs fcol" style="left:359px;top:2146px"><h4>Quick Links</h4><ul><li>Photo gallery</li><li>About us</li><li>Services</li><li>Policies</li></ul></div>
  <div class="abs fcol" style="left:524px;top:2146px"><h4>Links</h4><ul><li>Monthly newsletter</li><li>Unavailable dates</li><li>Introduction (welcome)</li><li>Payment methods</li></ul></div>
  <div class="abs fcol" style="left:729px;top:2146px"><h4>Resources</h4><ul><li>Term of Use</li><li>Privacy Policy</li><li>Contact Us</li></ul></div>
  <div class="abs fcol" style="left:886px;top:2146px"><h4>Follow Us</h4><p>Please sign up here for offers</p><div class="social"><i></i><i></i><i></i><i></i></div></div>

  <div class="abs bottombar">© 2016 Birchfordpawhaven.com&nbsp; All right reserved&nbsp; Term of Use</div>
</footer>

</body>
</html>
```